Veldmark Supplies Business Card

Professional business card that stand out to our potential customers. Front and back with clean modern design

Industry/Entity Type

Oil and gas

Contact Information for Business Card

Name, address, website , office phone and cell number

Requirements
Must have
• Editable files for each employee

```html
<!DOCTYPE html>
<html lang="en">
<head>
<meta charset="utf-8">
<title>Veldmark Supplies Business Card</title>
<link href="https://fonts.googleapis.com/css2?family=Montserrat:wght@500;600;800&display=swap" rel="stylesheet">
<style>
  :root {
    --brand-blue: #0eafd4;
    --brand-red: #ec1c24;
    --card-white: #ffffff;
    --ink: #1a1a1a;
    --stage: #3a3835;
  }
  * { margin: 0; padding: 0; box-sizing: border-box; }
  html, body { width: 1200px; height: 900px; overflow: hidden; }
  body {
    background: var(--stage);
    font-family: 'Montserrat', Arial, sans-serif;
    position: relative;
  }
  .card {
    position: absolute;
    left: 320px;
    width: 560px;
    height: 320px;
    border-radius: 22px;
    overflow: hidden;
  }
  .card-back {
    top: 100px;
    background: var(--brand-blue);
    display: flex;
    align-items: center;
    justify-content: center;
  }
  .card-front {
    top: 470px;
    background: var(--card-white);
  }
  .brand-lockup {
    display: flex;
    align-items: center;
    gap: 12px;
    white-space: nowrap;
  }
  .brand-square {
    width: 26px;
    height: 26px;
    background: var(--brand-red);
    flex: none;
  }
  .brand-name {
    font-weight: 800;
    text-transform: uppercase;
    letter-spacing: 1px;
  }
  .card-back .brand-square { background: var(--card-white); }
  .card-back .brand-name { color: var(--card-white); font-size: 34px; }
  .card-front .brand-lockup {
    position: absolute;
    left: 38px;
    top: 118px;
    gap: 8px;
  }
  .card-front .brand-square { width: 14px; height: 14px; }
  .card-front .brand-name { color: var(--brand-red); font-size: 15px; letter-spacing: 0.5px; }
  .divider {
    position: absolute;
    left: 258px;
    top: 36px;
    width: 36px;
    height: 160px;
  }
  .contact {
    position: absolute;
    left: 306px;
    top: 26px;
    color: var(--ink);
    font-weight: 500;
    font-size: 12.5px;
    line-height: 1.3;
    white-space: nowrap;
  }
  .person-name {
    color: var(--brand-red);
    font-weight: 800;
    font-size: 21px;
    letter-spacing: 0.5px;
  }
  .person-title { font-size: 13px; margin-bottom: 8px; }
  .address { margin-bottom: 8px; }
  .contact-list { list-style: none; }
  .contact-list li {
    display: flex;
    align-items: center;
    gap: 8px;
    margin-bottom: 3px;
  }
  .contact-icon {
    width: 15px;
    height: 15px;
    flex: none;
  }
  .web-domain { color: var(--brand-red); }
  .wave {
    position: absolute;
    left: 0;
    bottom: 0;
    width: 560px;
    height: 100px;
  }
</style>
</head>
<body>
  <section class="card card-back">
    <div class="brand-lockup">
      <span class="brand-square"></span>
      <span class="brand-name">Veldmark Supplies</span>
    </div>
  </section>

  <section class="card card-front">
    <div class="brand-lockup">
      <span class="brand-square"></span>
      <span class="brand-name">Veldmark Supplies</span>
    </div>

    <svg class="divider" viewBox="0 0 36 160" aria-hidden="true">
      <line x1="2" y1="0" x2="20" y2="160" stroke="var(--brand-blue)" stroke-width="1.5"/>
      <line x1="10" y1="25" x2="24" y2="145" stroke="var(--brand-red)" stroke-width="1.5"/>
      <line x1="24" y1="10" x2="34" y2="115" stroke="var(--brand-red)" stroke-width="1.5"/>
    </svg>

    <div class="contact">
      <p class="person-name">DANA HOLLOWAY</p>
      <p class="person-title">President</p>
      <p class="address">2740 Ridgeline Ave, Ste<br>210, Austin, TX 78701</p>
      <ul class="contact-list">
        <li>
          <svg class="contact-icon" viewBox="0 0 16 16" aria-hidden="true"><rect width="16" height="16" fill="var(--brand-red)"/><path d="M4 5c0-1 1-1.5 4-1.5S12 4 12 5v1h-2.5V5h-3v1H4zM4.5 7h7l1 5h-9z" fill="#fff"/></svg>
          555-214-3097
        </li>
        <li>
          <svg class="contact-icon" viewBox="0 0 16 16" aria-hidden="true"><rect width="16" height="16" fill="var(--brand-red)"/><rect x="5" y="3" width="6" height="10" rx="1" fill="none" stroke="#fff" stroke-width="1.3"/></svg>
          000-000-9999
        </li>
        <li>
          <svg class="contact-icon" viewBox="0 0 16 16" aria-hidden="true"><rect width="16" height="16" fill="var(--brand-red)"/><rect x="3" y="4.5" width="10" height="7" fill="none" stroke="#fff" stroke-width="1.2"/><path d="M3 4.5l5 4 5-4" fill="none" stroke="#fff" stroke-width="1.2"/></svg>
          info@example-youremail.com
        </li>
        <li>
          <svg class="contact-icon" viewBox="0 0 16 16" aria-hidden="true"><rect width="16" height="16" fill="var(--brand-red)"/><circle cx="8" cy="8" r="4.5" fill="none" stroke="#fff" stroke-width="1.2"/><path d="M3.5 8h9M8 3.5v9" stroke="#fff" stroke-width="1"/></svg>
          <span>www.<span class="web-domain">example-yourwebsite</span>.com</span>
        </li>
      </ul>
    </div>

    <svg class="wave" viewBox="0 0 560 100" preserveAspectRatio="none" aria-hidden="true">
      <path d="M0 85 C150 72 300 72 400 38 C450 20 500 12 560 15 L560 100 L0 100 Z" fill="var(--brand-blue)"/>
      <path d="M0 72 C160 60 300 56 385 12 C305 52 160 70 0 88 Z" fill="var(--brand-red)"/>
    </svg>
  </section>
</body>
</html>
```